Redesign two existing website pages and one new landing page for dental office

I need to redesign two webpages on my dental website, the Home page (http://velbridgedental.com) and the Dental Implant Services page (http://www.velbridgedental.com/dental-implant-services) and also create a landing page for the Dental Implant Services page.

Please use the same color scheme, slogans and subtitles for the redesign pages and create a reserved video spot on each page. The video spots should not be too big but not too small either and positioned in a central key location on each of the pages. The final redesigned pages should communicate leadership, confidence and trust.

The new landing page for the Dental implant Services page must not have any hyperlinks on the page and must entice the viewer to give name and email before downloading a "Free" eBook called "Is a Fuller Smile Worth the Wait?" Any added photo images to this new page must be smiling.
Updates

Project Deadline Extended Reason: I got feedback that my project was not long enough so I'm extending it by 5 days. Added Thursday, April 16, 2015

Target Market(s)

People who are middle-age to seniors.

Industry/Entity Type

Dental

Coding

Coded - Design and coding required

Number of Pages Required

3 page

Requirements
Must have
• Compatible with existing website colors and theme.

```html
<!DOCTYPE html>
<html lang="en">
<head>
<meta charset="utf-8">
<title>Velbridge Dental Care</title>
<link href="https://fonts.googleapis.com/css2?family=Open+Sans:wght@300;400;600;700&display=swap" rel="stylesheet">
<style>
:root{
  --teal:#2f6b5e;
  --teal-dark:#24544a;
  --teal-light:#5f9c8b;
  --ink:#2a2a2a;
  --muted:#777;
  --bar:#262626;
  --footer:#333333;
  --panel:#eef2f1;
  --white:#ffffff;
}
*{margin:0;padding:0;box-sizing:border-box}
html,body{width:712px;height:1200px;overflow:hidden}
body{font-family:'Open Sans',sans-serif;color:var(--ink);background:var(--white);position:relative}
.abs{position:absolute}
.topbar{left:0;top:0;width:712px;height:22px;background:var(--bar);color:#aaa;font-size:7.5px}
.topbar .welcome{left:66px;top:6px}
.topbar .links{right:64px;top:6px;display:flex;gap:18px}
.topbar .links span{display:flex;align-items:center;gap:5px}
.header{left:0;top:22px;width:712px;height:80px;background:var(--white)}
.brand{left:66px;top:30px;font-size:24px;font-weight:300;color:var(--teal-light);display:flex;align-items:center;gap:8px}
.brand .mark{width:10px;height:10px;border-radius:50%;background:var(--teal-light)}
.callus{right:64px;top:9px;text-align:right;font-size:8px;color:#333;line-height:1.4}
.callus .phone{font-size:12px;color:var(--teal-light);font-weight:400}
.social{right:64px;top:54px;display:flex;gap:3px}
.social i{width:15px;height:15px;border-radius:50%;background:#3b82c4;display:block}
.nav{left:0;top:102px;width:712px;height:31px;background:linear-gradient(#427f70,#2b5d52)}
.nav ul{list-style:none;display:flex;position:absolute;left:66px;top:0}
.nav li{width:97px;height:31px;line-height:31px;text-align:center;color:#fff;font-size:8.5px;font-weight:600;border-left:1px solid rgba(0,0,0,.18);border-right:1px solid rgba(255,255,255,.08)}
.nav li.active{background:rgba(0,0,0,.12)}
.hero{left:0;top:133px;width:712px;height:277px;background:linear-gradient(90deg,#eef1f1,#dbe3e4 60%,#cbd6d8);box-shadow:inset 0 -3px 4px rgba(0,0,0,.25);overflow:hidden}
.hero-photo{left:330px;top:0;width:382px;height:274px;background:linear-gradient(90deg,rgba(226,232,232,0) 0%,#e2d4c8 22%,#d7bca7 45%,#cfd6cc 70%,#cad3d4 100%)}
.hero h1{left:66px;top:84px;font-size:23px;font-weight:400;color:#333;line-height:1.18}
.hero h1 strong{color:var(--teal);font-weight:600;display:block}
.btn{left:66px;top:155px;width:150px;height:30px;background:var(--teal-dark);color:#fff;font-size:9.5px;font-weight:600;text-align:center;line-height:30px;border-radius:2px}
.dots{left:71px;top:253px;display:flex;gap:3px}
.dots i{width:5px;height:5px;border-radius:50%;background:#aaa;display:block}
.dots i:first-child{background:#333}
.features{left:0;top:410px;width:712px;height:232px;background:var(--panel)}
.feature{top:0;width:204px;height:232px;padding:26px 0 0 0}
.feature+.feature{border-left:1px solid #dfe5e4}
.feature h2{font-size:11.5px;font-weight:600;color:#222;margin-bottom:13px}
.frame{width:174px;background:#fff;padding:3px;box-shadow:0 1px 3px rgba(0,0,0,.2)}
.frame div{width:100%;height:78px}
.feature h3{font-size:9.3px;font-weight:400;margin:12px 0 5px;white-space:nowrap}
.feature p{font-size:7.3px;color:#888;line-height:1.6;width:180px}
.feature .more{font-size:7.5px;font-weight:600;margin-top:7px;color:#222}
.services{left:0;top:642px;width:712px;height:292px;background:linear-gradient(#fff 50%,#e5eeec)}
.services h2{width:712px;top:30px;text-align:center;font-size:23px;font-weight:300;color:var(--teal-light)}
.services h2 strong{font-weight:600;color:var(--teal-dark)}
.services .intro{left:150px;top:66px;width:412px;text-align:center;font-size:8px;color:#777;line-height:1.6}
.service{top:127px;width:150px;margin-left:-75px;text-align:center}
.service .avatar{width:56px;height:56px;border-radius:50%;margin:0 auto 17px}
.service h3{font-size:10.5px;font-weight:600;color:#222;margin-bottom:7px}
.service li{list-style:none;font-size:8px;color:#777;line-height:1.6}
.news{left:0;top:934px;width:712px;height:28px;background:var(--bar);color:#ddd;font-size:7.5px}
.news .text{left:70px;top:9px}
.news strong{font-weight:700;font-size:8.5px;color:#fff;margin-right:4px}
.news .arrows{right:82px;top:6px;display:flex;gap:3px}
.footer{left:0;top:962px;width:712px;height:203px;background:var(--footer);color:#bbb}
.footer h4{font-size:11.5px;font-weight:400;color:#fff;top:22px}
.footer p,.footer .post{font-size:7.3px;line-height:1.65}
.thumb{left:66px;top:45px;width:59px;height:53px}
.post{left:270px;display:flex;gap:7px;align-items:center;width:170px}
.post .date{width:36px;height:36px;background:#262626;color:#bbb;text-align:center;font-size:13px;line-height:1.1;padding-top:4px;flex:none}
.post .date small{display:block;font-size:7.5px}
.map{left:475px;top:45px;width:173px;height:71px;background:linear-gradient(135deg,#e6ebe0,#dbe1d6)}
.contact{left:475px;top:128px;width:175px;font-size:7.3px;line-height:1.65;border-collapse:collapse}
.contact td{padding-right:6px;vertical-align:top}
.contact td:first-child{width:37px}
.copy{left:0;top:1165px;width:712px;height:35px;background:#2b2b2b;color:#999;font-size:7.5px;text-align:center;line-height:35px;border-top:1px solid #3a3a3a}
</style>
</head>
<body>

<div class="abs topbar">
  <span class="abs welcome">Welcome To Velbridge Dental Care...!</span>
  <div class="abs links">
    <span><svg width="6" height="10" viewBox="0 0 6 10"><rect x=".5" y=".5" width="5" height="9" rx="1" fill="none" stroke="#aaa"/></svg>Get Dr.Velbridge Mobile App</span>
    <span><svg width="8" height="10" viewBox="0 0 8 10"><rect x=".5" y=".5" width="7" height="9" fill="none" stroke="#aaa"/><path d="M2 3h4M2 5h4M2 7h4" stroke="#aaa"/></svg>Patient online Forms</span>
  </div>
</div>

<header class="abs header">
  <div class="abs brand"><span class="mark"></span>Velbridge Dental Care</div>
  <div class="abs callus">Call Us Today!<br><span class="phone">(555) 214 7730</span><br>Crestfield, TX 75510, United States</div>
  <div class="abs social"><i></i><i style="background:#35a8d6"></i><i style="background:#d9493a"></i><i style="background:#1c83b5"></i></div>
</header>

<nav class="abs nav">
  <ul>
    <li class="active">HOME</li><li>ABOUT US</li><li>DENTAL SERVICES</li><li>OUR BLOG</li><li>CONTACT US</li><li>TESTIMONIALS</li>
  </ul>
</nav>

<section class="abs hero">
  <div class="abs hero-photo" role="img" aria-label="Photo of a smiling multi-generation family group"></div>
  <h1 class="abs">Life-Changing Family<strong>Dental Care In Crestfield</strong></h1>
  <div class="abs btn">REQUEST AN APPOINTMENT</div>
  <div class="abs dots"><i></i><i></i><i></i><i></i></div>
</section>

<section class="abs features">
  <div class="abs feature" style="left:66px">
    <h2>DENTAL HYGIENE SERVICES</h2>
    <div class="frame"><div role="img" aria-label="Photo of children brushing their teeth" style="background:linear-gradient(135deg,#e9ddd2,#c9a78c)"></div></div>
    <h3>Achieve Better Health With Prevention</h3>
    <p>Lorem ipsum dolor sit amet, consectetur adipiscing elit, sed do eiusmod tempor incididunt ut labore et dolore magna aliqua...</p>
    <div class="more">Read More »</div>
  </div>
  <div class="abs feature" style="left:255px;padding-left:15px;width:204px">
    <h2>DENTAL EMERGENCY SERVICES</h2>
    <div class="frame"><div role="img" aria-label="Photo of a woman holding her jaw in tooth pain" style="background:linear-gradient(135deg,#f2ebe6,#d79a6c)"></div></div>
    <h3>Stop Pain From Tooth Trauma &amp; Infection</h3>
    <p>Lorem ipsum dolor sit amet, consectetur adipiscing elit, sed do eiusmod tempor incididunt ut labore et dolore magna aliqua...</p>
    <div class="more">Read More »</div>
  </div>
  <div class="abs feature" style="left:459px;padding-left:15px;width:210px">
    <h2>WELCOME TO OUR PRACTICE</h2>
    <div class="frame" style="position:relative"><div role="img" aria-label="Video still of a dentist examining a smiling patient" style="height:154px;background:linear-gradient(135deg,#6a8aa0,#d8c8bd 60%,#e8e4e2)"></div>
      <svg style="position:absolute;left:68px;top:59px" width="38" height="38" viewBox="0 0 38 38"><circle cx="19" cy="19" r="19" fill="rgba(40,40,40,.6)"/><path d="M15 11l12 8-12 8z" fill="#fff"/></svg>
    </div>
  </div>
</section>

<section class="abs services">
  <h2 class="abs">OUR <strong>SERVICES</strong></h2>
  <p class="abs intro">Lorem ipsum dolor sit amet, consectetur adipiscing elit, sed do eiusmod tempor incididunt ut labore et dolore magna aliqua. Ut enim ad minim veniam, quis nostrud exercitation ullamco laboris nisi ut aliquip ex ea commodo consequat.</p>
  <div class="abs service" style="left:132px">
    <div class="avatar" role="img" aria-label="Portrait of a smiling senior woman" style="background:radial-gradient(#e5c6ae,#c49b80)"></div>
    <h3>BEAUTIFUL DENTURES</h3>
    <ul><li>What is a Denture?</li><li>Who Needs a Denture?</li><li>Just How Are Dentures Made?</li></ul>
  </div>
  <div class="abs service" style="left:282px">
    <div class="avatar" role="img" aria-label="Portrait of a smiling woman" style="background:radial-gradient(#f0d8c8,#b37b5b)"></div>
    <h3>COSMETIC DENTISTRY</h3>
    <ul><li>Whiten Your Teeth</li><li>Porcelain Veneers</li><li>Clear Aligner Therapy Orthodontics</li></ul>
  </div>
  <div class="abs service" style="left:431px;width:160px;margin-left:-80px">
    <div class="avatar" role="img" aria-label="Portrait of a smiling young woman" style="background:radial-gradient(#d9a88c,#5a2a24)"></div>
    <h3>DENTAL IMPLANT SERVICES</h3>
    <ul><li>Anchorage to the jaw bone</li><li>Replaces 1 or more missing teeth</li><li>Stabilizes loose, floppy dentures</li></ul>
  </div>
  <div class="abs service" style="left:582px">
    <div class="avatar" role="img" aria-label="Portrait of a relaxed dental patient" style="background:radial-gradient(#eeded2,#c8a896)"></div>
    <h3>SEDATION DENTISTRY</h3>
    <ul><li>Control Dental Fear with Sedation Dentistry</li><li>Dental Pain Management</li><li>Relaxed and Tranquil Treatment</li></ul>
  </div>
</section>

<div class="abs news">
  <div class="abs text"><strong>LATEST NEWS:</strong> Lorem ipsum dolor sit amet, consectetur adipisicing elit, sed do eiusmod tempor incididunt ut labore et dolore magna aliqua.</div>
  <div class="abs arrows">
    <svg width="15" height="15" viewBox="0 0 15 15"><circle cx="7.5" cy="7.5" r="7" fill="none" stroke="#888"/><path d="M8.5 4.5l-3 3 3 3" fill="none" stroke="#aaa"/></svg>
    <svg width="15" height="15" viewBox="0 0 15 15"><circle cx="7.5" cy="7.5" r="7" fill="none" stroke="#888"/><path d="M6.5 4.5l3 3-3 3" fill="none" stroke="#aaa"/></svg>
  </div>
</div>

<footer class="abs footer">
  <h4 class="abs" style="left:66px">Don't Wait 'til it Hurts!</h4>
  <div class="abs thumb" role="img" aria-label="Photo of a woman with tooth pain" style="background:linear-gradient(135deg,#ece4de,#c79d84)"></div>
  <p class="abs" style="left:132px;top:44px;width:112px">Lorem ipsum dolor sit amet, consectetur adipiscing elit, sed do eiusmod tempor incididunt ut labore et dolore magna aliqua...</p>
  <p class="abs" style="left:66px;top:108px;width:178px">Lorem ipsum dolor sit amet, consectetur adipiscing elit, sed do eiusmod tempor incididunt ut labore et dolore magna aliqua...</p>

  <h4 class="abs" style="left:270px">Recent Blog Posts</h4>
  <div class="abs post" style="top:45px"><div class="date">15<small>April</small></div><span>Conscious Sedation: A Way to Deal with Anxiety at the Dentist's Office</span></div>
  <div class="abs post" style="top:87px"><div class="date">15<small>April</small></div><span>Pediatric Dentists and Their Importance in Today's World</span></div>
  <div class="abs post" style="top:128px"><div class="date">15<small>April</small></div><span>Conscious Sedation: A Way to Deal with Anxiety at the Dentist's Office</span></div>

  <h4 class="abs" style="left:475px">Contact Us</h4>
  <div class="abs map" role="img" aria-label="Street map showing the office location"></div>
  <table class="abs contact">
    <tr><td>Address:</td><td>4820 Harbor Road, Ste. #120, Crestfield, TX 75510</td></tr>
    <tr><td>Email:</td><td>info@velbridgedental.com</td></tr>
    <tr><td>Phone:</td><td>(555) 214 7730</td></tr>
    <tr><td>Fax:</td><td>(555) 214 7730</td></tr>
  </table>
</footer>

<div class="abs copy">Copyrights © 2015 Velbridge Dental Care, Northgate Medical Group - All Rights reserved</div>

</body>
</html>
```